Vertical Banner

I need an eye-catching banner created for street fairs, indoor and outdoor events to draw attention to our language school. It will be to print on this banner (specs included):
https://www.banvoxprint.com/tag/617/Retractable-Banners/product/5174-46/Economy-Retractor-Banner-Display-27-09

I want the banner to be:
- SIMPLE
- Eye catching (not busy with too many pictures or information)
- It should say at top prominently: "Come learn a language!" and have our name.
- Below these languages should be large and eye-catching: Spanish, Chinese, French, Russian, German, Italian, Farsi, Turkish, Portuguese, ASL, Cantonese, Japanese, Korean, Vietnamese, Arabic, Dutch, more... (if some need to be cut our because of overcrowding let me know OR we can make some big and others small)
- Below this it should have GROUP & PRIVATE LESSONS
- It should be colorful and make people think of things international - perhaps national flags in background? Or images of world famous monuments? Could be image of adutls in a classroom. Sth that gets people excited about travel and language learning
- It should have our contact info VERY large at bottom:
Tovira Languages -
San Francisco, Silicon Valley & New York City
www.toviralanguagesf.com
415-629-5140
info@toviralanguagesf.com
(this can be smaller)
Four Wexmoor Plaza
Lobby 3
San Francisco, CA 94187

Hey Designers, please feel free to do a rough take on it. I don't need you to spend too much time, just give me a general idea of how you would make it look, then i know we can go from there later and refine it. Feel free to make it more of a quick sketch to show how you would do it.

Target Market(s)

adults from about 25-55 years old, educated, employed and typically world travellers

Industry/Entity Type

School

Colors
86cfc6
00a990
cadf82
acd036
9bcb3c
fbed22
f78f20
ffc214
f37122

Requirements
Must have
• Must be simple! Too many banners put way too much information and pictures. I want someone to walk by and immediately know we teach foreign languages. Must have bright colors and large font for languages offered
Should not have
• Should not be too full of images and design that distract the viewer from seeing the main thing I want them to see: that we teacher languages

```html
<!DOCTYPE html>
<html lang="en">
<head>
<meta charset="utf-8">
<title>Tovira Languages – Vertical Banner</title>
<link rel="stylesheet" href="https://fonts.googleapis.com/css2?family=Anton&family=Oswald:wght@500;600&family=Lobster&family=Roboto+Condensed:wght@700&display=swap">
<style>
  :root {
    --green: #0a8a3a;
    --red: #e3001b;
    --blue: #1f72c4;
    --yellow: #ffe600;
    --white: #ffffff;
    --ink: #1b1b1b;
    --stage: #e3e5e8;
    --sky-top: #2f86d6;
    --sky-mid: #8cc3ee;
    --sky-low: #f2f6fa;
  }
  * { box-sizing: border-box; margin: 0; padding: 0; }
  html, body { width: 1200px; height: 1175px; overflow: hidden; }
  body {
    background: var(--stage);
    position: relative;
  }
  .banner {
    position: absolute;
    left: 370px;
    top: 20px;
    width: 460px;
    height: 1135px;
    display: flex;
    flex-direction: column;
    background: var(--blue);
  }
  .brand {
    height: 200px;
    background: var(--green);
    display: flex;
    flex-direction: column;
    align-items: center;
    justify-content: center;
  }
  .brand-name {
    font-family: "Oswald", sans-serif;
    font-weight: 600;
    color: var(--white);
    font-size: 66px;
    line-height: 0.98;
    text-align: center;
  }
  .rule { height: 8px; background: var(--yellow); }
  .headline {
    height: 190px;
    background: var(--red);
    display: flex;
    flex-direction: column;
    align-items: center;
    justify-content: center;
    font-family: "Anton", sans-serif;
    color: var(--white);
    text-transform: uppercase;
    line-height: 1;
  }
  .headline-top { font-size: 64px; letter-spacing: 0.5px; }
  .headline-main { font-size: 86px; letter-spacing: 0.5px; }
  .languages {
    padding: 22px 18px 0;
    height: 232px;
    font-family: "Oswald", sans-serif;
    font-weight: 500;
    color: var(--white);
    font-size: 24px;
    line-height: 39px;
    text-align: center;
  }
  .lang-row .sep { color: var(--yellow); padding: 0 6px; }
  .lessons {
    height: 82px;
    display: flex;
    align-items: center;
    justify-content: center;
  }
  .lessons-ribbon { position: relative; width: 420px; height: 62px; }
  .lessons-ribbon svg { position: absolute; inset: 0; }
  .lessons-label {
    position: absolute; inset: 0;
    display: flex; align-items: center; justify-content: center;
    font-family: "Lobster", cursive;
    font-size: 31px;
    color: var(--white);
  }
  .scene {
    height: 256px;
    background: linear-gradient(180deg, var(--sky-top) 0%, var(--sky-mid) 55%, var(--sky-low) 100%);
  }
  .contact {
    flex: 1;
    background: var(--green);
    color: var(--white);
    font-family: "Roboto Condensed", sans-serif;
    font-weight: 700;
    text-align: center;
    display: flex;
    flex-direction: column;
    justify-content: center;
    gap: 2px;
    font-size: 19px;
    line-height: 1.2;
  }
  .contact-row { display: flex; justify-content: center; align-items: center; gap: 6px; }
  .contact-row svg { width: 15px; height: 15px; flex: none; }
  .contact-email { font-size: 16px; }
  .contact-address { font-size: 20px; }
</style>
</head>
<body>
  <main class="banner">
    <header class="brand">
      <div class="brand-name">Tovira<br>Languages</div>
    </header>
    <div class="rule"></div>
    <section class="headline">
      <div class="headline-top">Come learn a</div>
      <div class="headline-main">Language!</div>
    </section>
    <section class="languages">
      <div class="lang-row">Spanish<span class="sep">|</span>Chinese<span class="sep">|</span>French<span class="sep">|</span>Russian</div>
      <div class="lang-row">German<span class="sep">|</span>Italian<span class="sep">|</span>Farsi<span class="sep">|</span>Turkish<span class="sep">|</span>ASL</div>
      <div class="lang-row">Portuguese<span class="sep">|</span>Cantonese<span class="sep">|</span>Japanese</div>
      <div class="lang-row">Korean<span class="sep">|</span>Arabic<span class="sep">|</span>Dutch</div>
      <div class="lang-row">Vietnamese<span class="sep">|</span>more...</div>
    </section>
    <section class="lessons">
      <div class="lessons-ribbon">
        <svg viewBox="0 0 420 62" preserveAspectRatio="none" aria-hidden="true">
          <polygon points="0,8 420,0 408,27 420,54 0,62 12,35" fill="var(--white)"/>
          <polygon points="4,14 416,6 406,29 416,48 4,56 14,35" fill="var(--red)"/>
        </svg>
        <div class="lessons-label">Group &amp; Private Lessons</div>
      </div>
    </section>
    <div class="scene" role="img" aria-label="Photo of many national flags on poles against a blue sky"></div>
    <footer class="contact">
      <div class="contact-row">San Francisco, Silicon Valley &amp; New York City</div>
      <div class="contact-row">
        <svg viewBox="0 0 16 16" aria-hidden="true"><circle cx="8" cy="8" r="8" fill="var(--white)"/><path d="M5 4.2l1.6-.4 1 2.2-1 .8a5 5 0 0 0 2.6 2.6l.8-1 2.2 1-.4 1.6c-3.6.2-7-3.2-6.8-6.8z" fill="var(--green)"/></svg>
        <span>415-629-5140</span>
        <svg viewBox="0 0 16 16" aria-hidden="true"><circle cx="8" cy="8" r="7" fill="none" stroke="var(--white)" stroke-width="1.4"/><ellipse cx="8" cy="8" rx="3" ry="7" fill="none" stroke="var(--white)" stroke-width="1.2"/><line x1="1" y1="8" x2="15" y2="8" stroke="var(--white)" stroke-width="1.2"/></svg>
        <span>www.toviralanguagesf.com</span>
      </div>
      <div class="contact-row contact-email">
        <svg viewBox="0 0 16 16" aria-hidden="true"><circle cx="8" cy="8" r="7" fill="none" stroke="var(--white)" stroke-width="1.4"/><rect x="4" y="5.5" width="8" height="5.5" fill="none" stroke="var(--white)" stroke-width="1.1"/><path d="M4 5.5l4 3 4-3" fill="none" stroke="var(--white)" stroke-width="1.1"/></svg>
        <span>info@toviralanguagesf.com</span>
      </div>
      <div class="contact-row contact-address">Four Wexmoor Plaza, Lobby 3</div>
      <div class="contact-row contact-address">San Francisco, CA 94187</div>
    </footer>
  </main>
</body>
</html>
```